Specialist Recruitment Process Outsourcing (RPO) company needs a modern, sleek website

We need a website which showcases our service offering, describes our onshore and offshore options. Our service is basically building teams of recruiters who become the outsourced (but in-house) recruiter for that specific client. Our logo colours include a light, bright green and a dark/midnight blue. This company will be targeting companies who need help with recruitment in technology, finance, engineering and other white collar industries. We are looking for a look and feeling that communicates cutting edge technology with a bright, energetic appeal. I will include some logo design files to work with.

Target Market(s)

Businesses: start ups who need to grow their staff, SMEs with regular recruitment needs, and larger businesses

Industry/Entity Type

Recruitment

Coding

Coded - Design and coding required

Number of Pages Required

4 page

Font styles to use
Sans Serif

Requirements
Must have
• Landing page should be highly visual, either with dynamic image or scrolling stills accompanies by our core service offering, values, and benefits.

A Services page will allows more detail about what we do, with a call to action.

A User Stories page will showcase some examples of how our services will help certain types of businesses.

Onshore/Offshore page will breakdown the benefits of both approaches and how combinations can work well.

Should fit the colour theming of our logo (files uploaded).

Nice to have
• Imagery can be both around business and people. We are looking for more of a "startup" feel than a corporate-y feel.

```html
<!DOCTYPE html>
<html lang="en">
<head>
<meta charset="utf-8">
<title>Crewline — Recruitment Process Outsourcing</title>
<link href="https://fonts.googleapis.com/css2?family=Montserrat:wght@400;500;600;700&display=swap" rel="stylesheet">
<style>
:root{
  --green:#00f2a2;
  --navy:#0f1134;
  --navy-deep:#0c0e2c;
  --ink:#14162f;
  --text:#3a3c4c;
  --white:#ffffff;
}
*{box-sizing:border-box;margin:0;padding:0}
html,body{width:1200px;height:3505px;overflow:hidden}
body{font-family:'Montserrat',sans-serif;color:var(--ink);background:var(--white);position:relative}
a{color:inherit;text-decoration:none}

/* header */
.site-header{position:absolute;left:0;top:0;width:1200px;height:120px;background:var(--white)}
.site-header .rule-green{position:absolute;left:0;top:0;width:600px;height:3px;background:var(--green)}
.site-header .rule-navy{position:absolute;left:600px;top:0;width:600px;height:3px;background:var(--navy)}
.brand{position:absolute;left:172px;top:44px;display:flex;align-items:center;gap:10px;font-weight:600;font-size:17px;letter-spacing:5px;color:var(--navy)}
.brand .mark{width:12px;height:12px;background:var(--green)}
.main-nav{position:absolute;left:475px;top:51px;display:flex;gap:16px;font-size:14px;font-weight:500;color:var(--ink)}
.main-nav .active{color:var(--green);text-decoration:underline;text-underline-offset:3px}

/* hero */
.hero{position:absolute;left:0;top:120px;width:1200px;height:519px;
  background:radial-gradient(circle at 860px 260px,#2e6f92 0,#1b3f63 160px,#122846 320px,#0b1a32 520px);}
.hero-title{position:absolute;left:172px;top:118px;font-size:50px;font-weight:700;letter-spacing:10px;color:var(--green)}
.hero-sub{position:absolute;left:172px;top:198px;font-size:20px;line-height:31px;font-weight:500;color:var(--white)}
.btn{display:inline-block;background:var(--green);color:var(--navy);font-weight:500;border-radius:2px;text-align:center}
.hero .btn{position:absolute;left:172px;top:294px;width:126px;height:55px;line-height:55px;font-size:17px}

/* section headings */
.section-title{position:absolute;left:0;width:1200px;text-align:center;font-size:39px;font-weight:700;color:var(--ink)}
.heading-diamond{position:absolute;width:70px;height:70px;transform:rotate(45deg);border:10px solid rgba(20,22,47,.05)}

/* offer cards */
.offer-card{position:absolute;width:422px;height:422px}
.offer-card .shape{position:absolute;left:62px;top:62px;width:298px;height:298px;background:var(--white);transform:rotate(45deg);border-radius:8px;box-shadow:0 0 22px rgba(0,0,0,.12)}
.offer-card .icon{position:absolute;left:133px;top:-40px;width:156px;height:156px}
.offer-card h3{position:absolute;left:0;top:195px;width:422px;text-align:center;font-size:26px;font-weight:600}
.offer-card p{position:absolute;left:61px;top:249px;width:300px;text-align:center;font-size:15px;line-height:24.5px;color:var(--text)}
.offer-card .more{position:absolute;left:0;top:337px;width:422px;text-align:center;font-size:15px;font-weight:600}
.offer-card .pin{position:absolute;left:184px;top:374px;width:54px;height:54px}
.offer-card.benefits h3,.offer-card.benefits .more{color:var(--green)}

/* what we do */
.what-we-do{position:absolute;left:0;top:1347px;width:1200px;height:497px;background:linear-gradient(90deg,#cfd0d4 0,#d6d7da 55%,#e8e8ea 100%)}
.what-we-do .photo{position:absolute;left:610px;top:0;width:590px;height:497px;
  background:linear-gradient(90deg,rgba(214,215,218,0) 0,#d9d3cb 20%,#cbbfae 55%,#8b8f72 100%)}
.what-we-do h2{position:absolute;left:174px;top:88px;font-size:40px;font-weight:700}
.what-we-do p{position:absolute;left:172px;top:162px;width:460px;font-size:14.3px;line-height:25.8px;color:var(--ink)}
.what-we-do .btn{position:absolute;left:172px;top:340px;width:126px;height:55px;line-height:55px;font-size:17px}

/* stories */
.story{position:absolute;top:2101px;width:300px;height:300px}
.story .shape{position:absolute;left:44px;top:44px;width:212px;height:212px;transform:rotate(45deg);background:var(--white);border-radius:6px;box-shadow:0 0 20px rgba(0,0,0,.12)}
.story .portrait{position:absolute;left:96px;top:-12px;width:108px;height:108px;transform:rotate(45deg);border:2px solid var(--navy);border-radius:6px;background:linear-gradient(135deg,#c8c8c8,#6f6f6f)}
.story h3{position:absolute;left:0;top:127px;width:300px;text-align:center;font-size:20px;font-weight:600}
.story p{position:absolute;left:35px;top:162px;width:230px;text-align:center;font-size:10.5px;line-height:18px;color:var(--text)}
.story .more{position:absolute;left:0;top:229px;width:300px;text-align:center;font-size:11px;font-weight:600}
.story .quote{position:absolute;left:120px;top:259px;width:60px;height:60px}
.story.featured .shape{left:39px;top:39px;width:222px;height:222px;background:var(--green);border:2px solid var(--navy);box-shadow:none}
.story.featured p{color:#1c5b4b}
.carousel-arrow{position:absolute;top:2225px;width:30px;height:52px}

/* onshore */
.onshore{position:absolute;left:0;top:2517px;width:1200px;height:497px;
  background:linear-gradient(90deg,#2b3444 0,#3a2d38 30%,#46262f 60%,#2a2c36 100%)}
.onshore-diamond{position:absolute;left:312px;top:2552px;width:576px;height:576px}
.onshore-title{position:absolute;left:0;top:2694px;width:1200px;text-align:center;font-size:40px;font-weight:700;color:var(--white)}
.onshore-copy{position:absolute;left:425px;top:2769px;width:350px;text-align:center;font-size:14.3px;line-height:25.5px;color:var(--white)}
.onshore-btn{position:absolute;left:546px;top:2922px;width:108px;height:45px;line-height:45px;font-size:15px}

/* footer */
.site-footer{position:absolute;left:0;top:3014px;width:1200px;height:491px;background:var(--navy-deep);border-top:3px solid var(--green)}
.footer-brand{position:absolute;left:172px;top:3286px;display:flex;align-items:center;gap:14px;font-size:30px;font-weight:600;letter-spacing:8px;color:var(--green)}
.footer-brand .mark{width:16px;height:16px;background:var(--green)}
.footer-heading{position:absolute;top:3179px;font-size:18px;font-weight:600;color:var(--green)}
.quick-links{position:absolute;left:516px;top:3219px;list-style:none;font-size:14px;line-height:25.3px;color:var(--white)}
.newsletter-input{position:absolute;left:712px;top:3224px;width:316px;height:55px;border:2px solid var(--green);border-radius:4px;color:var(--white);font-size:14px;line-height:51px;padding-left:13px}
.newsletter-submit{position:absolute;left:712px;top:3291px;width:114px;height:56px;line-height:56px;font-size:16px}
.footer-rule{position:absolute;left:172px;top:3418px;width:856px;height:1px;background:var(--green)}
.copyright{position:absolute;left:0;top:3457px;width:1200px;text-align:center;font-size:13px;font-weight:600;color:var(--green)}
</style>
</head>
<body>

<header class="site-header">
  <div class="rule-green"></div><div class="rule-navy"></div>
  <div class="brand"><span class="mark"></span>CREWLINE</div>
  <nav class="main-nav">
    <a class="active">HOME</a><a>SERVCIES</a><a>WHAT WE DO</a><a>USER STORIES</a><a>ONSHORE</a><a>CONTACT</a>
  </nav>
</header>

<section class="hero" role="img" aria-label="Hand touching a glowing digital interface of recruitment icons on a dark blue background">
  <h1 class="hero-title">CREWLINE</h1>
  <p class="hero-sub">We are a Specialist Recruitment Process<br>Outsourcing (RPO) company</p>
  <a class="btn">READ MORE</a>
</section>

<div class="heading-diamond" style="left:565px;top:712px"></div>
<h2 class="section-title" style="top:722px">WHAT WE OFFER</h2>

<article class="offer-card values" style="left:172px;top:820px">
  <div class="shape"></div>
  <svg class="icon" viewBox="0 0 156 156">
    <rect x="23" y="23" width="110" height="110" rx="8" transform="rotate(45 78 78)" fill="#14162f"/>
    <circle cx="78" cy="78" r="28" fill="none" stroke="#00f2a2" stroke-width="3"/>
    <path d="M78 44v10M78 102v10M44 78h10M102 78h10" stroke="#00f2a2" stroke-width="3"/>
    <circle cx="78" cy="68" r="6" fill="#00f2a2"/>
    <path d="M67 92v-10a11 11 0 0 1 22 0v10z" fill="#00f2a2"/>
  </svg>
  <h3>VALUES</h3>
  <p>Duis aute irure dolor in reprehenderit in voluptate velit esse cillum dolore eu fugiat nulla pariatur.</p>
  <div class="more">READ MORE</div>
  <svg class="pin" viewBox="0 0 54 54"><rect x="11" y="11" width="32" height="32" rx="3" transform="rotate(45 27 27)" fill="#14162f"/><path d="M19 20l8 8 8-8M19 27l8 8 8-8" fill="none" stroke="#fff" stroke-width="2"/></svg>
</article>

<article class="offer-card benefits" style="left:608px;top:820px">
  <div class="shape"></div>
  <svg class="icon" viewBox="0 0 156 156">
    <rect x="23" y="23" width="110" height="110" rx="8" transform="rotate(45 78 78)" fill="#00f2a2"/>
    <rect x="58" y="50" width="36" height="50" rx="2" fill="none" stroke="#14162f" stroke-width="3"/>
    <path d="M64 80h20M64 88h16" stroke="#14162f" stroke-width="3"/>
    <circle cx="72" cy="64" r="5" fill="#14162f"/>
    <path d="M100 62L82 96l-2 8 7-5 18-33z" fill="#14162f"/>
  </svg>
  <h3>BENEFITS</h3>
  <p>Duis aute irure dolor in reprehenderit in voluptate velit esse cillum dolore eu fugiat nulla pariatur.</p>
  <div class="more">READ MORE</div>
  <svg class="pin" viewBox="0 0 54 54"><rect x="11" y="11" width="32" height="32" rx="3" transform="rotate(45 27 27)" fill="#00f2a2"/><path d="M19 20l8 8 8-8M19 27l8 8 8-8" fill="none" stroke="#fff" stroke-width="2"/></svg>
</article>

<section class="what-we-do">
  <div class="photo" role="img" aria-label="Smiling woman in glasses shaking hands across a desk in a bright office"></div>
  <div class="heading-diamond" style="left:280px;top:78px"></div>
  <h2>WHAT WE DO</h2>
  <p>Nemo enim ipsam voluptatem quia voluptas sit aspernatur aut odit aut fugit, sed quia consequuntur magni dolores eos qui ratione vo luptatem sequi nesciunt. Neque porro quisquam est, qui dolorem ipsum quia dolor sit amet, consectetur, adipisci velit, sed quia non numquam eius modi tempora incidunt ut labore et dolore magnam aliquam quaerat voluptatem.</p>
  <a class="btn">READ MORE</a>
</section>

<div class="heading-diamond" style="left:565px;top:1930px"></div>
<h2 class="section-title" style="top:1940px">USER STORIES</h2>

<svg class="carousel-arrow" style="left:70px" viewBox="0 0 30 52"><path d="M27 2L3 26l24 24" fill="none" stroke="#14162f" stroke-width="2.5"/></svg>
<svg class="carousel-arrow" style="left:1097px" viewBox="0 0 30 52"><path d="M3 2l24 24L3 50" fill="none" stroke="#14162f" stroke-width="2.5"/></svg>

<article class="story" style="left:181px">
  <div class="shape"></div>
  <div class="portrait" role="img" aria-label="Portrait of a young man"></div>
  <h3>OWEN CALDER</h3>
  <p>Duis aute irure dolor in reprehenderit in voluptate velit esse cillum dolore eu fugiat nulla pariatur.</p>
  <div class="more">READ MORE</div>
  <svg class="quote" viewBox="0 0 60 60"><rect x="12" y="12" width="36" height="36" rx="3" transform="rotate(45 30 30)" fill="#00f2a2"/><text x="30" y="41" text-anchor="middle" font-family="Montserrat,sans-serif" font-weight="700" font-size="28" fill="#14162f">”</text></svg>
</article>

<article class="story featured" style="left:450px">
  <div class="shape"></div>
  <div class="portrait" role="img" aria-label="Portrait of a smiling young woman"></div>
  <h3>LENA</h3>
  <p>Duis aute irure dolor in reprehenderit in voluptate velit esse cillum dolore eu fugiat nulla pariatur.</p>
  <div class="more">READ MORE</div>
  <svg class="quote" viewBox="0 0 60 60"><rect x="12" y="12" width="36" height="36" rx="3" transform="rotate(45 30 30)" fill="#14162f"/><text x="30" y="41" text-anchor="middle" font-family="Montserrat,sans-serif" font-weight="700" font-size="28" fill="#ffffff">”</text></svg>
</article>

<article class="story" style="left:722px">
  <div class="shape"></div>
  <div class="portrait" role="img" aria-label="Portrait of a laughing young man in glasses"></div>
  <h3>RAFI</h3>
  <p>Duis aute irure dolor in reprehenderit in voluptate velit esse cillum dolore eu fugiat nulla pariatur.</p>
  <div class="more">READ MORE</div>
  <svg class="quote" viewBox="0 0 60 60"><rect x="12" y="12" width="36" height="36" rx="3" transform="rotate(45 30 30)" fill="#00f2a2"/><text x="30" y="41" text-anchor="middle" font-family="Montserrat,sans-serif" font-weight="700" font-size="28" fill="#14162f">”</text></svg>
</article>

<section class="onshore" role="img" aria-label="Two colleagues talking in a modern lounge office with red chairs"></section>

<footer class="site-footer"></footer>

<svg class="onshore-diamond" viewBox="0 0 576 576">
  <polygon points="288,8 568,288 288,568 8,288" fill="rgba(20,22,50,.82)" stroke="#00f2a2" stroke-width="11" stroke-linejoin="round"/>
</svg>
<h2 class="onshore-title">ONSHORE</h2>
<p class="onshore-copy">Nemo enim ipsam voluptatem quia voluptas sit aspernatur aut odit aut fugit, sed quia consequun tur magni dolores eos qui ratione vo luptatem sequi nesciunt. Neque porro quisquam est, qui do lorem ipsum quias.</p>
<a class="btn onshore-btn">READ MORE</a>

<div class="footer-brand"><span class="mark"></span>CREWLINE</div>
<h4 class="footer-heading" style="left:516px">QUICK LINKS</h4>
<ul class="quick-links">
  <li>HOME</li><li>SERVCIES</li><li>WHAT WE DO</li><li>USER STORIES</li><li>ONSHORE</li><li>CONTATCT</li>
</ul>
<h4 class="footer-heading" style="left:712px">NEWSLETTER</h4>
<div class="newsletter-input">Email</div>
<a class="btn newsletter-submit">SUBMIT</a>
<div class="footer-rule"></div>
<p class="copyright">Copyrights @ 2020 Crewline. All Rights Reserved.</p>

</body>
</html>
```